NZ First of it's kind solutions directory and marketplace for busy Mums needs a business card design

We need a business card design for our new nationwide business in NZ (long term plans to go global). We provide solutions to the everyday challenges that busy Mums face by connecting them with quality communities and suppliers of carefully selected, relevant products and services. We sell direct via our online marketplace. The final design should communicate our values of inclusivity, quality and smart solutions. Colours should incorporate our logo colour palette of #477077 and #6ba8b2. Our website is at https://www.brightnestmums.example

Target Market(s)

busy Mums, Age 28 – 50, female, income over $100K, location main centres NZ primarily but NZ wide. Is likely juggling work or career with a young family. Probably had hobbies which have fallen by the wayside.
-Wants to succeed in her chosen career without compromising on family life
-to successfully juggle her career without feeling like she is compromising her children
- Is time poor, something always has to give and it’s generally her health (she’ll stay up late, get stressed)
- probably ex corporate or professional career. Has discretional income

Industry/Entity Type

Business

Contact Information for Business Card

Lena Forbisher, Founder, BrightNestMums.example (Strapline Tap; Gather; Sorted), 47 Kowhai Terrace, Ellerslie, Auckland 1051, New Zealand. Mob: 021 483 517 Ph: +64 (0)9 571 4860

Font styles to use
Other font styles liked:
• Raleway, and/or Architects Daughter

Colors
00a990
33b8a4
86cfc6
cfeae6

Requirements
Must have
• the above details, streamline. the logo and colours associated with those logos
Should not have
• foil or metallic colours

```html
<!DOCTYPE html>
<html lang="en">
<head>
<meta charset="utf-8">
<title>BrightNest Mums – Business Card</title>
<link href="https://fonts.googleapis.com/css2?family=Nunito:ital,wght@0,800;1,400&family=Roboto:ital,wght@0,400;1,400&display=swap" rel="stylesheet">
<style>
  :root {
    --page-bg: #e9e9e9;
    --card-top: #41636b;
    --card-bottom: #3a5860;
    --ink: #ffffff;
    --ink-soft: #dde9eb;
    --accent: #6ba8b2;
  }
  * { box-sizing: border-box; margin: 0; padding: 0; }
  html, body {
    width: 1200px; height: 576px; overflow: hidden;
    background: var(--page-bg);
  }
  .canvas { position: relative; width: 1200px; height: 576px; }
  .card {
    position: absolute; top: 138px; height: 292px;
    border-radius: 12px;
    background: linear-gradient(180deg, var(--card-top), var(--card-bottom));
    color: var(--ink);
    overflow: hidden;
  }
  .card--front { left: 82px; width: 484px; }
  .card--back { left: 602px; width: 480px; }

  .brand {
    position: absolute; left: 0; right: 0; top: 108px;
    text-align: center;
  }
  .brand__name {
    font-family: "Nunito", sans-serif; font-weight: 800;
    font-size: 44px; line-height: 1; letter-spacing: -0.5px;
    color: var(--ink);
  }
  .brand__strapline {
    margin-top: 18px;
    font-family: "Roboto", sans-serif; font-size: 14px;
    letter-spacing: 0.38em; color: var(--ink-soft);
    padding-left: 0.38em;
  }

  .person {
    position: absolute; right: 260px; top: 111px; text-align: right;
  }
  .person__name {
    font-family: "Nunito", sans-serif; font-weight: 800;
    font-size: 19px; line-height: 1.1;
  }
  .person__role {
    font-family: "Roboto", sans-serif; font-style: italic;
    font-size: 11.5px; margin-top: 3px; color: var(--ink-soft);
  }
  .person__address {
    font-family: "Roboto", sans-serif; font-style: normal;
    font-size: 12px; line-height: 18px; margin-top: 8px; color: var(--ink-soft);
  }

  .contact {
    position: absolute; left: 246px; top: 114px; list-style: none;
    font-family: "Roboto", sans-serif; font-size: 12px; color: var(--ink-soft);
  }
  .contact__item { display: flex; align-items: center; height: 18.5px; }
  .contact__icon { width: 11px; height: 11px; margin-right: 7px; fill: var(--ink-soft); }
</style>
</head>
<body>
<main class="canvas">

  <section class="card card--front" aria-label="Card front">
    <div class="brand">
      <div class="brand__name">BrightNest Mums</div>
      <div class="brand__strapline">TAP | GATHER | SORTED</div>
    </div>
  </section>

  <section class="card card--back" aria-label="Card back">
    <div class="person">
      <div class="person__name">Lena Forbisher</div>
      <div class="person__role">Founder</div>
      <address class="person__address">47 Kowhai Terrace, Ellerslie,<br>Auckland 1051, New Zealand</address>
    </div>

    <ul class="contact">
      <li class="contact__item">
        <svg class="contact__icon" viewBox="0 0 12 12" aria-hidden="true"><path d="M3 0h6a1 1 0 0 1 1 1v10a1 1 0 0 1-1 1H3a1 1 0 0 1-1-1V1a1 1 0 0 1 1-1zm.5 1.5v7.5h5V1.5zM6 9.8a.7.7 0 1 0 0 1.4.7.7 0 0 0 0-1.4z"/></svg>
        021 483 517
      </li>
      <li class="contact__item">
        <svg class="contact__icon" viewBox="0 0 12 12" aria-hidden="true"><path d="M1 4c0-1.5 2.2-2.5 5-2.5S11 2.5 11 4v1H8.5V3.8h-5V5H1zM3 6h6l1.5 4.5h-9zM6 6.8a1.4 1.4 0 1 0 0 2.8 1.4 1.4 0 0 0 0-2.8z"/></svg>
        +64 (0)9 571 4860
      </li>
      <li class="contact__item">
        <svg class="contact__icon" viewBox="0 0 12 12" aria-hidden="true"><circle cx="6" cy="6" r="5.2" fill="none" stroke="currentColor" stroke-width="1" style="stroke:var(--ink-soft)"/><path d="M.8 6h10.4M6 .8c-2.6 3-2.6 7.4 0 10.4M6 .8c2.6 3 2.6 7.4 0 10.4" fill="none" style="stroke:var(--ink-soft)" stroke-width="0.9"/></svg>
        www.BrightNestMums.example
      </li>
      <li class="contact__item">
        <svg class="contact__icon" viewBox="0 0 12 12" aria-hidden="true"><path d="M0 2.5h12v7H0zm1 .8 5 3.4 5-3.4v-.1H1z"/></svg>
        lena@brightnestmums.example
      </li>
    </ul>
  </section>

</main>
</body>
</html>
```